Acoustic Jazz album needs cover design

The CD cover has five parts, each one has obligatory features:

I. Main cover

Title: Reflections: Morning Chants
Artist: Benedek Szurovy
Design image*

The main design motive should be something that suggests: happiness, freedom, health, balance, something like that. Please see my other covers at benedeksound.com/music. Please don’t use the same key elements as there.
I prefer zen-like, minimalist solutions.
NO stock images, please! Except for unrecognizable parts of something.

II. Cover inside

Track list (10 songs) with durations
All songs written by Benedek Szurovy
Copyright Benedeksound 2016.
Design image

III. Disc

Artist: Benedek Szurovy
All songs written by Benedek Szurovy (round on the edge)
Copyright Benedeksound 2016. (round on the edge)
www.benedeksound.com (round on the edge)

IV. Cover back

Track list (same as cover inside)
Copyright Benedeksound 2016.
www.benedeksound.com
design image (optional)
The paper of this page is longer than the main cover, because it is to be turned up when put in the CD case, and there is the saddle/spine with the name of the Artist and Title of the album. On both ends.

V. Under the disc

No words, only some design feature.

Important:
The main cover I need in RGB and also CMYK, all the others only CMYK.
I need the work file (cdr, ai or whatever you use)
I need the CMYK images prepared for printing (sizes set, and that little extra on the edges).
I need the RGB main cover cover in jpeg, 3000x3000 pixels.
That's all. :)

The most important of these all is of course the main cover RGB. Make this one first!

Here’s a sample to listen, it might inspire you:

https://www.filecrate.example/s/k27rmw81dpz4qtx/morning_chants_medley_benedek_szurovy_20160108.mp3?dl=0

And here’s the Benedek Szurovy logo:

https://www.filecrate.example/s/vn4hq02xlpe8tyr/Logo%20BS%20print%2020150216.psd?dl=0

If you take a closer look at my website, you can see the whole concept.

Good luck and enjoy!
Regards,
Benedek

Target Market(s)

New age spiritual people

Requirements
Nice to have
• "Simplicity, the ultimate sophistication."
• Don't overdose it with elements. Make it simple.

```html
<!DOCTYPE html>
<html lang="en">
<head>
<meta charset="utf-8">
<title>Reflections: Morning Chants — CD Packaging</title>
<link rel="stylesheet" href="https://fonts.googleapis.com/css2?family=Ubuntu:ital,wght@0,400;0,500;0,700;1,400&display=swap">
<style>
  :root{
    --canvas:#ececec;
    --paper:#ffffff;
    --paper-edge:#e4e4e6;
    --ink:#1f1f22;
    --ink-soft:#3a3a3e;
    --sky-light:#cfe7f7;
    --sky:#a9d2ee;
    --sky-deep:#8fbfe0;
    --shadow:rgba(0,0,0,.12);
    --rule:#bdbdc2;
    --accent:#f2b323;
  }
  *{margin:0;padding:0;box-sizing:border-box}
  html,body{width:1200px;height:1200px;overflow:hidden;background:var(--canvas)}
  body{position:relative;font-family:"Ubuntu",sans-serif;color:var(--ink)}

  .panel{
    position:absolute;
    background:radial-gradient(ellipse at 50% 45%,var(--paper) 55%,var(--paper-edge) 100%);
    box-shadow:0 3px 10px var(--shadow);
  }
  .front-cover{left:100px;top:165px;width:455px;height:400px}
  .back-cover{left:645px;top:165px;width:455px;height:400px}
  .inside-cover{left:30px;top:615px;width:430px;height:410px}
  .tray-inlay{left:465px;top:615px;width:460px;height:410px}

  .artist-mark{
    position:absolute;display:flex;align-items:center;gap:6px;
    font-weight:500;font-size:15px;color:var(--ink-soft);letter-spacing:.02em;
  }
  .artist-mark .dot{width:9px;height:9px;border-radius:50%;background:var(--accent)}
  .front-cover .artist-mark{left:0;right:0;top:60px;justify-content:center}

  .origami-bird{
    position:absolute;border-radius:46% 54% 40% 60% / 55% 45% 55% 45%;
    background:linear-gradient(135deg,var(--sky-light),var(--sky) 55%,var(--sky-deep));
  }
  .ground-shadow{
    position:absolute;height:4px;border-radius:50%;
    background:radial-gradient(ellipse,rgba(0,0,0,.16),transparent 70%);
  }
  .front-cover .origami-bird{left:135px;top:150px;width:235px;height:165px}
  .front-cover .ground-shadow{left:165px;top:350px;width:165px}
  .front-cover .album-title{
    position:absolute;left:0;right:0;top:368px;text-align:center;font-size:19px;
  }
  .album-title b{font-weight:700}

  .title-block{position:absolute;text-align:right}
  .title-block .lead{font-weight:700;font-size:20px;display:block;line-height:1.1}
  .title-block .sub{font-size:20px;display:block;line-height:1.2}
  .title-block .credit{font-size:9px;line-height:1.75;margin-top:6px;color:var(--ink-soft)}
  .title-block .site{font-weight:700;font-size:11px;margin-top:8px;letter-spacing:.03em}

  .back-cover .origami-bird{left:35px;top:40px;width:215px;height:180px}
  .back-cover .ground-shadow{left:70px;top:245px;width:145px}
  .back-cover .title-block{right:210px;top:272px}

  .track-list{position:absolute;list-style:none;font-size:10px;color:var(--ink-soft)}
  .track-list li{display:flex;height:18.8px;align-items:center}
  .track-list .no{width:18px;text-align:right;padding-right:7px;font-weight:700;color:var(--ink)}
  .track-list .name{width:98px}
  .track-list .time{font-style:italic}
  .back-cover .track-list{left:263px;top:140px}
  .inside-cover .track-list{left:218px;top:150px}

  .cloud-band{
    position:absolute;left:20px;right:10px;top:35px;height:85px;border-radius:50px 50px 8px 8px;
    background:linear-gradient(180deg,rgba(255,255,255,0),#f7f8fa 60%,#fbfbfc);
    box-shadow:inset 0 -6px 14px rgba(0,0,0,.04);
  }
  .inside-cover .title-block{right:225px;top:308px}
  .tray-inlay .cloud-band{left:30px;right:20px;top:35px;height:80px}

  .disc{position:absolute;left:780px;top:690px;width:420px;height:420px}
  .disc-face{position:absolute;inset:0}
  .disc .origami-bird{left:165px;top:35px;width:95px;height:70px}
  .disc .ground-shadow{left:180px;top:110px;width:65px}
  .disc .album-title{position:absolute;left:0;right:0;top:118px;text-align:center;font-size:14px}
  .disc .artist-mark{left:0;right:0;top:318px;justify-content:center;font-size:12px}
  .disc .artist-mark .dot{width:7px;height:7px}
</style>
</head>
<body>

<section class="panel front-cover" aria-label="Front cover">
  <div class="artist-mark"><span class="dot"></span>Benedek Szurovy</div>
  <div class="origami-bird" role="img" aria-label="Pale blue origami bird with white clouds on its wings"></div>
  <div class="ground-shadow"></div>
  <h1 class="album-title"><b>Reflections:</b> Morning Chants</h1>
</section>

<section class="panel back-cover" aria-label="Back cover">
  <div class="origami-bird" role="img" aria-label="Pale blue origami bird with white clouds on its wings"></div>
  <div class="ground-shadow"></div>
  <div class="title-block">
    <span class="lead">Reflections:</span>
    <span class="sub">Morning Chants</span>
    <p class="credit">All songs written by Benedek Szurovy<br>Copyright Benedeksound 2016</p>
    <p class="site">www.benedeksound.com</p>
  </div>
  <ol class="track-list">
    <li><span class="no">1</span><span class="name">Piano Relax</span><span class="time">5:30</span></li>
    <li><span class="no">2</span><span class="name">Relax dummy copy</span><span class="time">4:15</span></li>
    <li><span class="no">3</span><span class="name">Relax dummy</span><span class="time">6:10</span></li>
    <li><span class="no">4</span><span class="name">Dummy Relax</span><span class="time">3:45</span></li>
    <li><span class="no">5</span><span class="name">Piano Relax</span><span class="time">7:15</span></li>
    <li><span class="no">6</span><span class="name">Relax dummy copy</span><span class="time">5:30</span></li>
    <li><span class="no">7</span><span class="name">Relax dummy</span><span class="time">4:15</span></li>
    <li><span class="no">8</span><span class="name">Dummy Relax</span><span class="time">6:10</span></li>
    <li><span class="no">9</span><span class="name">Piano Relax</span><span class="time">3:45</span></li>
    <li><span class="no">10</span><span class="name">Relax dummy copy</span><span class="time">7:15</span></li>
    <li><span class="no">11</span><span class="name">Relax dummy</span><span class="time">7:15</span></li>
    <li><span class="no">12</span><span class="name">Dummy Relax</span><span class="time">5:30</span></li>
  </ol>
</section>

<section class="panel inside-cover" aria-label="Inside cover">
  <div class="cloud-band" role="img" aria-label="Soft white clouds along the top"></div>
  <ol class="track-list">
    <li><span class="no">1</span><span class="name">Piano Relax</span><span class="time">5:30</span></li>
    <li><span class="no">2</span><span class="name">Relax dummy copy</span><span class="time">4:15</span></li>
    <li><span class="no">3</span><span class="name">Relax dummy</span><span class="time">6:10</span></li>
    <li><span class="no">4</span><span class="name">Dummy Relax</span><span class="time">3:45</span></li>
    <li><span class="no">5</span><span class="name">Piano Relax</span><span class="time">7:15</span></li>
    <li><span class="no">6</span><span class="name">Relax dummy copy</span><span class="time">5:30</span></li>
    <li><span class="no">7</span><span class="name">Relax dummy</span><span class="time">4:15</span></li>
    <li><span class="no">8</span><span class="name">Dummy Relax</span><span class="time">6:10</span></li>
    <li><span class="no">9</span><span class="name">Piano Relax</span><span class="time">3:45</span></li>
    <li><span class="no">10</span><span class="name">Relax dummy copy</span><span class="time">7:15</span></li>
    <li><span class="no">11</span><span class="name">Relax dummy</span><span class="time">7:15</span></li>
    <li><span class="no">12</span><span class="name">Dummy Relax</span><span class="time">5:30</span></li>
  </ol>
  <div class="title-block">
    <span class="lead">Reflections:</span>
    <span class="sub">Morning Chants</span>
    <p class="credit">All songs written by Benedek Szurovy<br>Copyright Benedeksound 2016</p>
  </div>
</section>

<section class="panel tray-inlay" aria-label="Under the disc">
  <div class="cloud-band" role="img" aria-label="Soft white clouds along the top"></div>
</section>

<section class="disc" aria-label="Disc">
  <svg class="disc-face" viewBox="0 0 420 420" width="420" height="420">
    <defs>
      <path id="rim-arc" d="M 27 210 A 183 183 0 0 0 393 210"/>
    </defs>
    <circle cx="210" cy="210" r="203" fill="#fff" stroke="#b9b9be" stroke-width="1.5"/>
    <circle cx="210" cy="210" r="66" fill="none" stroke="#9a9aa0" stroke-width="1"/>
    <circle cx="210" cy="210" r="56" fill="#f1f1f3" stroke="#9a9aa0" stroke-width="1"/>
    <text font-family="Ubuntu, sans-serif" font-size="10.5" fill="#1f1f22" letter-spacing=".4">
      <textPath href="#rim-arc" startOffset="50%" text-anchor="middle">All songs written by <tspan font-weight="700">Benedek Szurovy</tspan>  -  Copyright <tspan font-weight="700">Benedeksound</tspan> 2016  -  www.benedeksound.com</textPath>
    </text>
  </svg>
  <div class="origami-bird" role="img" aria-label="Small pale blue origami bird with clouds"></div>
  <div class="ground-shadow"></div>
  <p class="album-title"><b>Reflections:</b> Morning Chants</p>
  <div class="artist-mark"><span class="dot"></span>Benedek Szurovy</div>
</section>

</body>
</html>
```